Harbourline Electrical Solutions

On one side. LOGO (underneath:) Commercial Industrial Residential

- NAME & CONTACT DETAILS

Marcus T. Hollings
Project Manager

(Cell icon) (441) 555-0187
(Email icon) hlelectricalsolutions@mailvento.com
(Facebook & Instagram icons )@hlelectricalsolutions

Other side: LOGO - underneath ELECTRICAL CONSTRUCTION & MAINTENANCE . LED LIGHTING & AUTOMATION . LIFE SAFETY SYSTEMS (FIRE ALARM / SECURITY) . DATA & COMMUNICATION

```html
<!DOCTYPE html>
<html lang="en">
<head>
<meta charset="utf-8">
<title>Harbourline Electrical Solutions – Business Card</title>
<link rel="stylesheet" href="https://fonts.googleapis.com/css2?family=Raleway:wght@400;600;700&family=Lato:wght@400&display=swap">
<style>
  :root {
    --bg: #2e2e2e;
    --card-white: #ffffff;
    --teal: #0f5268;
    --slate: #4a4a4a;
    --text-grey: #4d4d4d;
    --rule: #cfcfcf;
    --white: #ffffff;
  }
  * { margin: 0; padding: 0; box-sizing: border-box; }
  html, body { width: 1200px; height: 1200px; overflow: hidden; }
  body { background: var(--bg); position: relative; font-family: "Raleway", sans-serif; }

  .card { position: absolute; top: 310px; height: 594px; }
  .card-front { left: 234px; width: 364px; background: var(--card-white); }
  .card-back { left: 627px; width: 369px; background: var(--slate); overflow: hidden; }

  /* Front */
  .brand-name {
    position: absolute; top: 438px; left: 0; width: 100%;
    text-align: center; color: var(--teal);
    font-family: "Raleway", sans-serif; font-weight: 700;
    font-size: 22px; line-height: 27px; letter-spacing: 1px; text-transform: uppercase;
  }
  .card-front .brand-name { top: 128px; }
  .tagline {
    position: absolute; top: 206px; left: 0; width: 100%; text-align: center;
    font-family: "Lato", sans-serif; font-size: 15px; color: var(--text-grey);
  }
  .person-name {
    position: absolute; top: 354px; left: 0; width: 100%; text-align: center;
    font-weight: 700; font-size: 21px; color: var(--teal);
  }
  .person-title {
    position: absolute; top: 378px; left: 0; width: 100%; text-align: center;
    font-family: "Raleway", sans-serif; font-size: 17px; color: var(--text-grey);
  }
  .icon-row { position: absolute; left: 0; width: 100%; height: 30px; }
  .icon-row svg { display: block; margin: 0 auto; }
  .icon-row.social { top: 405px; }
  .icon-row.contact { top: 465px; }
  .contact-line {
    position: absolute; left: 0; width: 100%; text-align: center;
    font-family: "Raleway", sans-serif; font-size: 17px; color: var(--text-grey);
  }
  .handle { top: 437px; }
  .phone { top: 499px; }
  .email { top: 521px; }

  /* Back */
  .back-top { position: absolute; top: 0; left: 0; width: 100%; height: 238px; background: var(--teal); }
  .back-brand {
    position: absolute; top: 186px; left: 0; width: 100%; text-align: center;
    color: var(--white); font-weight: 700; font-size: 34px; line-height: 40px;
    text-transform: uppercase; letter-spacing: 1px;
  }
  .services {
    position: absolute; top: 414px; left: 0; width: 100%; text-align: center;
    list-style: none; color: var(--white); font-weight: 600; font-size: 17.5px; line-height: 21.5px;
  }
</style>
</head>
<body>
  <section class="card card-front">
    <div class="brand-name">Harbourline<br>Electrical Solutions</div>
    <p class="tagline">COMMERCIAL INDUSTRIAL RESIDENTIAL</p>
    <h1 class="person-name">MARCUS T. HOLLINGS</h1>
    <p class="person-title">Project Manager</p>

    <div class="icon-row social">
      <svg width="364" height="30" viewBox="0 0 364 30" aria-hidden="true">
        <line x1="112" y1="15" x2="150" y2="15" stroke="var(--rule)" stroke-width="1"/>
        <line x1="214" y1="15" x2="252" y2="15" stroke="var(--rule)" stroke-width="1"/>
        <circle cx="166" cy="15" r="12.5" fill="none" stroke="var(--teal)" stroke-width="1.5"/>
        <circle cx="198" cy="15" r="12.5" fill="none" stroke="var(--teal)" stroke-width="1.5"/>
      </svg>
    </div>
    <p class="contact-line handle">@hlelectricalsolutions</p>

    <div class="icon-row contact">
      <svg width="364" height="30" viewBox="0 0 364 30" aria-hidden="true">
        <line x1="112" y1="15" x2="150" y2="15" stroke="var(--rule)" stroke-width="1"/>
        <line x1="214" y1="15" x2="252" y2="15" stroke="var(--rule)" stroke-width="1"/>
        <circle cx="166" cy="15" r="12.5" fill="none" stroke="var(--teal)" stroke-width="1.5"/>
        <rect x="161" y="7" width="10" height="16" rx="2" fill="none" stroke="var(--teal)" stroke-width="1.5"/>
        <line x1="164.5" y1="20" x2="167.5" y2="20" stroke="var(--teal)" stroke-width="1.2"/>
        <circle cx="198" cy="15" r="12.5" fill="none" stroke="var(--teal)" stroke-width="1.5"/>
        <rect x="190" y="9.5" width="16" height="11" rx="1" fill="var(--teal)"/>
        <polyline points="190.5,10 198,16 205.5,10" fill="none" stroke="var(--white)" stroke-width="1.2"/>
      </svg>
    </div>
    <p class="contact-line phone">(441) 555-0187</p>
    <p class="contact-line email">hlelectricalsolutions@mailvento.com</p>
  </section>

  <section class="card card-back">
    <div class="back-top"></div>
    <div class="back-brand">Harbourline<br>Electrical Solutions</div>
    <ul class="services">
      <li>ELECTRICAL CONSTRUCTION</li>
      <li>MAINTENANCE</li>
      <li>LED LIGHTING &amp; AUTOMATION</li>
      <li>DATA &amp; COMMUNICATION</li>
      <li>LIFE SAFETY SYSTEMS</li>
      <li>(FIRE ALARM / SECURITY)</li>
    </ul>
  </section>
</body>
</html>
```